QUORVIN CAPABILITY STATEMENT “Shaping Lasting Links”

QUORVIN CAPABILITY STATEMENT
“Shaping Lasting Links”
Indigenous-Owned Telecommunications & Infrastructure Solutions Partner

COVER PAGE

Visual: Modern and clean design featuring telecom towers, wind turbines, civil infrastructure, roads, and community WiFi imagery.
Tagline: “Linking Places, Lifting Futures.”
Contact:
Website: www.quorvin.com.au
Email: info@quorvin.com.au
Phone: [Insert Main Number]
“Proudly Indigenous-Owned | Compliant with Aboriginal Procurement Policy (APP) & SME Policies”
INTRODUCTION

Quorvin is a 100% Indigenous-owned leader in comprehensive infrastructure solutions, specializing in telecommunications, civil works, renewable energy, structural engineering, and site development. With over a decade of experience, we deliver safe, reliable, and culturally respectful services across Australia, from urban centers to remote wind farms and heritage sites. Our mission: “To bridge infrastructure gaps while empowering Indigenous communities and fostering sustainable growth.”

CORE CAPABILITIES

TELECOMMUNICATIONS

Tower Builds & Maintenance: Structural engineering, geotechnical analysis, foundation mapping.
Community WiFi Projects: Enhancing digital inclusion in Indigenous and remote communities.
Fiber & Wireless Networks: End-to-end installation for Velonet, Satellite, and regional connectivity.
Height Safety Systems: Design, inspection, and certification of lad-safe safety infrastructure.
CIVIL & STRUCTURAL ENGINEERING

Foundations & Concreting: Reinforced slabs, grillage, geotech-to-construction turnkey solutions.
Site Development: Earthworks, drainage, and access road/track construction.
Wind Farm Infrastructure: Reinforcing towers and integrating power systems for high-wind environments.
ROAD & ACCESS TRACK CONSTRUCTION

Construction of durable access roads and tracks: For remote projects and urban settings.
Remediation of existing tracks: Upgrading for environmental compliance and sustainability.
Facilitating logistics and site access: Particularly in challenging terrain.
POWER & ELECTRICAL SYSTEMS

Off-grid energy solutions: Solar hybrid systems, electrical structural engineering.
Grid upgrades: Ensuring compliance with AS/NZS standards and facilitating connection upgrades.
SITE REFURBISHMENT & DEMOLITION

Comprehensive refurbishment and demolition services: For outdated telecom sites and structures.
Environmentally responsible dismantling: Focused on recycling materials and minimizing land impact.
EMERGENCY RESPONSE SERVICES

24/7 Rapid Response: Over 450 callouts annually; 4,000+ emergencies resolved nationwide.
Disaster Recovery: Comprehensive support during floods, bushfires for Velonet, Marvaske, Trilumen, and regional clients.
PROJECT EXPERIENCE

Heritage Tower Upgrade

Enhanced safety and technology on culturally significant heritage sites, preserving their integrity.
Wind Farm Deployment

Delivered power, fiber, and reinforced foundations for large-scale renewable energy projects in high-wind environments.
Regional Fibre Network

Laid 200km of fiber in flood-prone regions, ensuring critical infrastructure resilience.
Indigenous Community WiFi & Connectivity

Installed sustainable WiFi networks to bridge the digital divide, supporting education, health, and business activities.
Site Demolition & Refurbishment

Safely decommissioned aging telecom sites and structures across Australia, emphasizing land reuse and environmental care.
Access Track Construction & Remediation

Developed new access roads and refurbished existing tracks to facilitate project logistics, particularly in remote or environmentally sensitive areas.
Key Stats:
+600 sites supported | 10-year Velonet partner | 98% client retention | Over 20 Indigenous community WiFi deployments

COMMITMENT TO SAFETY & QUALITY

“Pause Twice, Work Wise” Protocol: Enforced pre-task risk assessments to ensure safety at every stage.
Certifications: ISO 45001 (Safety) | ISO 9001 (Quality Management).
Safety Culture: Regular safety audits, Indigenous-led training programs, and safety initiatives focused on community well-being.
INDIGENOUS INCLUSION & COMMUNITY IMPACT

Elders Guidance Council: Provides guidance on community engagement, cultural sensitivity, and social responsibility.
Supplier Diversity: 30% procurement from Indigenous-owned businesses, fostering economic growth.
Regional Employment: 65% of our workforce originates from local communities, creating sustainable jobs.
Testimonial: “Quorvin’s partnership empowered our community with jobs and infrastructure that respects our land.” – Local Indigenous Leader

CONTACT & SERVICE AREAS

Headquarters: [Insert Address] | ABN: [Insert ABN]

24/7 Emergency Support: [Insert Dedicated Emergency Line]

Certifications & Registrations:

Trade Circle Registered, First Enterprise Register (FER)
SERVICE AREAS

National Coverage with Regional Expertise:
Major Cities: Sydney, Melbourne, Brisbane, Perth, Adelaide, Darwin, Hobart.
Regional & Remote Areas: Pilbara, Kimberley, Far North Queensland, Outback NSW.
Disaster Zones: Rapid response teams deployed nationwide for bushfire and flood incidents.
EMERGENCY SUPPORT

SLA Guarantee: 90% of emergencies addressed within 4 hours.
Partners Supported: Velonet, Marvaske, Trilumen, regional councils.
This capability statement reflects our commitment to quality, safety, and community engagement across all levels of operation, ensuring that we empower the communities we serve while maintaining the highest standards of service delivery.

Target Market(s)

Government Agencies: Especially those seeking to comply with Indigenous Procurement Policies. Telecommunication Operators: Such as Velonet, Marvaske, and Trilumen for infrastructure deployment. Indigenous Communities: Projects aimed at enhancing connectivity and digital inclusion. Utilities and Energy Providers: For power and electrical infrastructure projects. Construction and Engineering Firms: Seeking collaboration on civil and structural infrastructure projects.

Industry/Entity Type

Telecommunications and Infrastructure Development: Focused on service delivery in various contexts, including urban settings, remote locations, and Indigenous community projects. Renewable Energy: This includes wind and solar infrastructure linked to telecommunications enhancements. Civil Engineering: Related to building and maintaining essential infrastructure such as access roads and utility lines.

Font styles to use
Other font styles liked:
• Bubbleboddy neue

Requirements
Must have
• Clear demonstration of Indigenous ownership and community engagement. Compliance with relevant safety and quality certifications (e.g., ISO 45001, ISO 9001). Showcase of core capabilities in telecommunications, civil engineering, and those specific to renewable energy. Visuals that reflect the diverse range of services offered (like telecom towers and community WiFi installations).
Nice to have
• Interactive elements such as hyperlinks to project case studies or client testimonials. Infographics or visual data to highlight key statistics and project success rates. Cultural motifs or imagery that reflect Indigenous heritage and inclusion in design aspirations. QR codes that link to videos or more detailed project descriptions for digital formats.
Should not have
• Clutter or excessive text that detracts from the main messages. Generic stock images that don’t align with the specific projects or Indigenous culture. Technical jargon that could confuse stakeholders unfamiliar with industry-specific terms. Overemphasis on competitors; the focus should remain on Quorvin's unique strengths and contributions.

```html
<!DOCTYPE html>
<html lang="en">
<head>
<meta charset="utf-8">
<title>Quorvin Capability Statement – Services &amp; Commitments</title>
<link href="https://fonts.googleapis.com/css2?family=Barlow:wght@400;600;700&family=Righteous&display=swap" rel="stylesheet">
<style>
  :root {
    --red: #c8161d;
    --red-dark: #a6151b;
    --ink: #111111;
    --body: #4a4a4a;
    --paper: #ffffff;
    --charcoal: #2b2b2b;
    --green: #2f7d32;
    --gold: #f2b41c;
  }
  * { margin: 0; padding: 0; box-sizing: border-box; }
  html, body { width: 928px; height: 1200px; overflow: hidden; background: var(--paper); }
  .page {
    position: relative; width: 928px; height: 1200px; overflow: hidden;
    font-family: "Barlow", Arial, sans-serif; color: var(--body);
  }
  .motif { position: absolute; }
  .motif--top { top: 0; left: 658px; }
  .motif--bottom { left: 0; bottom: 0; }

  .service { position: absolute; left: 88px; display: flex; gap: 18px; }
  .service__icon { width: 62px; height: 62px; flex: none; }
  .service__title { color: var(--red-dark); font-weight: 700; font-size: 21px; line-height: 26px; }
  .service__text { font-size: 18.5px; line-height: 25.5px; white-space: nowrap; }
  .service--height { top: 168px; }
  .service--foundations { top: 274px; }

  .section-title {
    position: absolute; left: 80px; font-family: "Righteous", Arial, sans-serif;
    font-size: 27px; letter-spacing: -0.6px; color: var(--ink); text-transform: uppercase;
    line-height: 30px; white-space: nowrap;
  }
  .break-fix-title { top: 377px; }
  .safety-title { top: 737px; }
  .quality-title { top: 868px; }
  .transparency-title { top: 973px; }

  .bullets { position: absolute; left: 172px; top: 422px; list-style: none; width: 668px; }
  .bullets li {
    position: relative; padding-left: 17px; font-size: 18.5px; line-height: 25.5px;
    margin-bottom: 14.5px;
  }
  .bullets li::before {
    content: ""; position: absolute; left: 0; top: 10px; width: 6px; height: 6px;
    border-radius: 50%; background: var(--red);
  }

  .commitment { position: absolute; left: 80px; font-size: 18.5px; line-height: 25.5px; white-space: nowrap; }
  .safety-text { top: 767px; }
  .quality-text { top: 898px; }
  .transparency-text { top: 1004px; }

  .badges { position: absolute; left: 0; top: 0; width: 928px; height: 1200px; pointer-events: none; }
</style>
</head>
<body>
<div class="page">

  <svg class="motif motif--top" width="270" height="104" viewBox="0 0 270 104" role="img" aria-label="Red Indigenous dot-painting chevron motif">
    <defs>
      <linearGradient id="motifTop" x1="0" y1="0" x2="1" y2="1">
        <stop offset="0" stop-color="#e0252b"/><stop offset="1" stop-color="#c8161d"/>
      </linearGradient>
    </defs>
    <polygon points="0,0 58,0 135,58 212,0 270,0 135,102" fill="url(#motifTop)"/>
  </svg>

  <svg class="motif motif--bottom" width="266" height="102" viewBox="0 0 266 102" role="img" aria-label="Red Indigenous dot-painting chevron motif">
    <defs>
      <linearGradient id="motifBottom" x1="0" y1="1" x2="1" y2="0">
        <stop offset="0" stop-color="#c8161d"/><stop offset="1" stop-color="#e0252b"/>
      </linearGradient>
    </defs>
    <polygon points="0,102 131,1 266,102 196,102 131,52 62,102" fill="url(#motifBottom)"/>
  </svg>

  <div class="service service--height">
    <svg class="service__icon" viewBox="0 0 62 62" aria-hidden="true">
      <circle cx="31" cy="31" r="31" fill="var(--red-dark)"/>
      <rect x="27" y="15" width="16" height="32" rx="2" fill="none" stroke="#fff" stroke-width="3"/>
      <path d="M36 22h7M36 29h7M36 36h7" stroke="#fff" stroke-width="2.5"/>
      <path d="M20 46V18M15 23l5-6 5 6" fill="none" stroke="#fff" stroke-width="3"/>
    </svg>
    <div>
      <h2 class="service__title">Height Safety:</h2>
      <p class="service__text">Design, test, and implementation of height safety systems.</p>
      <p class="service__text">Inspection and replacement of steprail systems on towers.</p>
    </div>
  </div>

  <div class="service service--foundations">
    <svg class="service__icon" viewBox="0 0 62 62" aria-hidden="true">
      <circle cx="31" cy="31" r="31" fill="var(--red-dark)"/>
      <circle cx="31" cy="27" r="15" fill="none" stroke="#fff" stroke-width="3" stroke-dasharray="5 3"/>
      <path d="M23 28l8-7 8 7v7H23z" fill="#fff"/>
      <path d="M13 42c6 0 9 3 13 3h10c3 0 3 3 0 3H27M36 45l10-5c3-1 4 2 2 3l-12 7H20l-7-3" fill="none" stroke="#fff" stroke-width="2.5"/>
    </svg>
    <div>
      <h2 class="service__title">Foundations:</h2>
      <p class="service__text">Foundation solutions, from small slabs, piers, Geotech to turnkey construction jobs.</p>
      <p class="service__text">Including grillage, floating slabs, Security Fencing, Gantry</p>
    </div>
  </div>

  <h2 class="section-title break-fix-title">Emergency Break Fix Services</h2>
  <ul class="bullets">
    <li>24/7 support with a rolling fleet of six trucks.</li>
    <li>Over 450 callouts per year.</li>
    <li>Purposely equipped and modified vehicles for the task.</li>
    <li>Over 4,000 emergency break fix calls answered in eight years.</li>
    <li>Supporting over 600 sites with fast, quality emergency break fix services.</li>
    <li>Experience with Trilumen on their expanding fibre and wireless network.</li>
    <li>Experience with Marvaske on the Velonet infrastructure on satellite and fixed<br>wireless for the last 10 years during floods and bush fires.</li>
  </ul>

  <h2 class="section-title safety-title">Commitment to Safety</h2>
  <div class="commitment safety-text">
    <p>Prioritising the safety of our team and the communities we serve.</p>
    <p>Stringent safety protocols to ensure a secure working environment.</p>
    <p>"Pause Twice, Work Wise" culture.</p>
  </div>

  <h2 class="section-title quality-title">Commitment to Quality</h2>
  <div class="commitment quality-text">
    <p>Delivering top-notch workmanship.</p>
    <p>Skilled team using best practices and the latest technology.</p>
  </div>

  <h2 class="section-title transparency-title">Commitment to Transparency</h2>
  <div class="commitment transparency-text">
    <p>Honesty and openness in all business dealings.</p>
    <p>Keeping clients informed at every stage of the project.</p>
  </div>

  <svg class="badges" viewBox="0 0 928 1200" role="img" aria-label="Partner, program and certification badges">
    <circle cx="291" cy="1146" r="22" fill="var(--gold)"/>
    <rect x="343" y="1129" width="156" height="45" rx="3" fill="var(--charcoal)"/>
    <rect x="517" y="1132" width="145" height="38" rx="19" fill="var(--green)"/>
    <circle cx="706" cy="1151" r="26" fill="none" stroke="var(--red)" stroke-width="3"/>
    <rect x="750" y="1128" width="80" height="37" rx="2" fill="var(--red)"/>
    <rect x="853" y="1127" width="39" height="48" rx="6" fill="var(--red)"/>
  </svg>

</div>
</body>
</html>
```